Website Design for WestaKolory.pl – Luxury Wedding Car Rental with Chauffeur

We are looking for a talented designer to create a modern, elegant, and fully responsive website for our new brand – WestyKolory.pl. We are a premium car rental platform in Poland, offering luxury and exotic vehicles exclusively for weddings. All cars come with a professional chauffeur, ensuring a high-end, stress-free, and stylish experience.
Website Purpose:
The website should present our offering in a luxurious, clear, and inspiring way. It must build trust, highlight the prestige of our brand, and encourage inquiries. Our target audience includes engaged couples, wedding planners, and clients seeking a truly exceptional vehicle for their special day.
Design Requirements:
Style: modern, elegant, minimalist
Color palette: white, black, gold, optionally silver – refined and luxurious
Typography: clean, modern, high-end
Layout: clear, intuitive, with large car images and well-defined sections
Fully responsive (desktop, tablet, mobile)
Bilingual layout (Polish/English) must be considered
Pages to Design:
Homepage
About Us
Fleet Overview
Individual Car Pages
Services (Weddings, Photo Shoots, Film Rentals)
Why Us / Unique Selling Points
Contact
FAQ
Inspiration:
Luxury automotive brands (e.g. Varnel-Hoske, Corvash, Elbrin Tusko)
High-end wedding websites
Minimalist layouts with large visuals and elegant typography
Additional Notes:
The design should evoke the emotions of a wedding day – elegance, uniqueness, style, and class. Please avoid flashy colors, excessive graphic effects, or overly decorative elements. Subtlety, prestige, and sophistication are key.

```html
<!DOCTYPE html>
<html lang="en">
<head>
<meta charset="utf-8">
<title>WestaKolory.pl – Luxury Wedding Cars with Chauffeur</title>
<link rel="stylesheet" href="https://fonts.googleapis.com/css2?family=Marcellus&family=Montserrat:wght@400;500;600&display=swap">
<style>
:root{
  --gold:#d5b95d;
  --gold-dark:#b99b3c;
  --ink:#1e1e1e;
  --muted:#6b6b6b;
  --line:#e4e4e4;
  --soft:#f3f3f3;
  --footer:#1c1c1c;
  --white:#ffffff;
}
*{margin:0;padding:0;box-sizing:border-box}
html,body{width:1200px;height:4882px;overflow:hidden}
body{position:relative;background:var(--white);color:var(--ink);font-family:"Montserrat",sans-serif;font-size:12px;line-height:1.6}
.serif{font-family:"Marcellus",serif;font-weight:400}
.abs{position:absolute}
.btn{position:absolute;display:flex;align-items:center;justify-content:center;font-size:12px;font-weight:600;color:var(--ink)}
.btn-gold{background:var(--gold)}
.btn-line{border:1.5px solid var(--ink);background:var(--white)}
.eyebrow{color:var(--gold);font-size:12px;font-weight:500}
.h2{font-family:"Marcellus",serif;font-size:38px;line-height:1.15;color:var(--ink)}
.center{text-align:center;left:0;width:1200px}
.lead{color:var(--muted);font-size:12px;line-height:1.65}
.photo{position:absolute}
.floral{position:absolute;border-radius:50%;background:radial-gradient(circle,rgba(230,200,195,.45) 0%,rgba(210,225,205,.35) 45%,rgba(255,255,255,0) 72%)}
.badge{width:80px;height:80px;border-radius:50%;background:var(--gold);display:flex;align-items:center;justify-content:center}
.badge svg{width:40px;height:40px}
.badge-sm{width:58px;height:58px}
.badge-sm svg{width:28px;height:28px}

/* header */
.site-header{position:absolute;top:0;left:0;width:1200px;height:85px;background:var(--white);z-index:5}
.brand{position:absolute;left:76px;top:22px;display:flex;align-items:center;gap:10px;font-family:"Marcellus",serif;font-size:26px;color:var(--gold)}
.brand-dot{width:30px;height:30px;border-radius:50%;border:1.5px solid var(--gold)}
.main-nav{position:absolute;left:404px;top:32px;display:flex;gap:31px;font-size:12px}
.nav-cta{left:906px;top:21px;width:132px;height:42px;font-size:12px}
.lang{position:absolute;left:1062px;top:33px;font-size:11px;font-weight:600;display:flex;align-items:center;gap:6px}
.flag{width:18px;height:12px;background:linear-gradient(#1f3f8f 0 100%);position:relative}
.flag::after{content:"";position:absolute;inset:5px 0;background:#c8102e}

/* hero */
.hero-photo{left:0;top:85px;width:1200px;height:740px;background:linear-gradient(180deg,#b9c1c6 0%,#8b9296 40%,#4a4d4f 70%,#5e5b57 100%)}
.hero-card{position:absolute;left:0;top:260px;width:578px;height:318px;background:var(--white);border-radius:0 0 40px 0}
.hero-card h1{position:absolute;left:76px;top:34px;font-family:"Marcellus",serif;font-weight:400;font-size:54px;line-height:1.18}
.hero-card p{position:absolute;left:76px;top:162px;width:440px;font-size:11.5px;color:var(--muted);line-height:1.6}

/* services */
.service-col{position:absolute;top:1030px;width:300px;text-align:center}
.service-col .badge{margin:0 auto}
.service-col h3{font-family:"Marcellus",serif;font-weight:400;font-size:19px;margin-top:10px}
.service-col p{font-size:11px;color:var(--muted);margin-top:2px}
.vrule{position:absolute;width:1px;background:var(--line)}

/* arch images */
.arch{border-radius:200px 200px 0 0}
.arch-frame{position:absolute;border:1.5px solid var(--gold);border-radius:200px 200px 0 0}

/* about */
.about-text{position:absolute;left:591px;width:470px}
.about-text p{font-size:11.5px;color:var(--muted);line-height:1.7}

/* feature columns */
.feature-col{position:absolute;top:1920px;width:250px;text-align:center}
.feature-col .badge{margin:0 auto}
.feature-col h3{font-family:"Marcellus",serif;font-weight:400;font-size:19px;margin-top:14px}
.feature-col p{font-size:11px;color:var(--muted);line-height:1.6;margin-top:2px}

/* collection */
.collection-band{left:0;top:2198px;width:1200px;height:232px;background:var(--soft)}
.collection-photo{left:0;top:2430px;width:1200px;height:580px;background:linear-gradient(180deg,#d9dde2 0%,#efe0b8 35%,#e6d6ad 60%,#8b5a4e 85%,#7a4e44 100%)}

/* why */
.why-item{position:absolute;left:122px;width:430px;height:74px;border-bottom:1px solid var(--line);display:flex;gap:14px}
.why-item:last-of-type{border-bottom:none}
.why-item h3{font-family:"Marcellus",serif;font-weight:400;font-size:20px;line-height:1.2;margin-top:4px}
.why-item p{font-size:11px;color:var(--muted);margin-top:3px}

/* faq */
.faq-item{position:absolute;left:224px;width:752px;background:var(--soft)}
.faq-item h3{font-family:"Marcellus",serif;font-weight:400;font-size:18px;position:absolute;left:24px;top:12px}
.faq-item p{position:absolute;left:24px;top:48px;font-size:11px;color:var(--ink)}
.faq-item svg{position:absolute;right:24px;top:19px;width:12px;height:12px}

/* contact */
.contact-card{position:absolute;left:153px;top:4102px;width:467px;height:362px;background:var(--white);box-shadow:0 6px 30px rgba(0,0,0,.12);z-index:3}
.field{position:absolute}
.field label{font-size:9.5px;font-weight:500;display:block;margin-bottom:5px}
.field .box{background:#efefef;height:34px}

/* footer */
.site-footer{position:absolute;left:0;top:4444px;width:1200px;height:438px;background:var(--footer);color:var(--white)}
.foot-brand{position:absolute;left:76px;top:160px;display:flex;align-items:center;gap:12px;font-family:"Marcellus",serif;font-size:40px;color:var(--gold)}
.foot-brand .brand-dot{width:44px;height:44px}
.foot-col{position:absolute;top:100px}
.foot-col h4{font-family:"Marcellus",serif;font-weight:400;font-size:23px;border-left:2px solid var(--gold);padding-left:8px;line-height:1}
.foot-col ul{list-style:none;margin-top:14px;padding-left:12px}
.foot-col li{font-size:10.5px;line-height:27px;color:#e8e8e8}
.contact-line{display:flex;gap:12px;font-size:10.5px;color:#e8e8e8;margin-top:14px;padding-left:8px;line-height:1.5}
.contact-line svg{width:11px;height:11px;flex:none;margin-top:3px}
.foot-rule{position:absolute;left:76px;top:370px;width:1048px;height:1px;background:#3a3a3a}
.copyright{position:absolute;left:0;width:1200px;top:392px;text-align:center;font-size:10.5px;color:#e8e8e8}
.to-top{position:absolute;left:1131px;top:345px;width:50px;height:50px;border-radius:50%;background:var(--gold);display:flex;align-items:center;justify-content:center}
</style>
</head>
<body>

<header class="site-header">
  <div class="brand"><span class="brand-dot"></span>WestaKolory.pl</div>
  <nav class="main-nav"><span>Home</span><span>About Us</span><span>Our Fleet</span><span>Services</span><span>Why Choose Us</span><span>FAQ</span></nav>
  <span class="btn btn-line nav-cta">Contact Us</span>
  <div class="lang"><span class="flag"></span>EN
    <svg width="9" height="6" viewBox="0 0 9 6"><path d="M1 1l3.5 3.5L8 1" stroke="#1e1e1e" stroke-width="1.5" fill="none"/></svg></div>
</header>

<!-- hero -->
<div class="photo hero-photo" role="img" aria-label="Bride and groom embracing beside a vintage silver wedding car on a cobbled street"></div>
<section class="hero-card">
  <h1>Luxury Cars for<br>Your Special Day</h1>
  <p>Arrive in timeless elegance. Our exclusive collection of wedding vehicles comes with a professional chauffeur to ensure a stylish stress free experience.</p>
  <span class="btn btn-gold" style="left:76px;top:236px;width:154px;height:41px">View Our Fleet</span>
  <span class="btn btn-line" style="left:241px;top:236px;width:131px;height:41px">Contact Us</span>
</section>

<!-- services -->
<div class="floral" role="img" aria-label="Watercolour floral decoration" style="left:900px;top:820px;width:320px;height:300px"></div>
<div class="abs center eyebrow" style="top:895px">Our Service</div>
<h2 class="abs center h2" style="top:918px">More Than Just a Ride</h2>
<p class="abs lead" style="left:250px;width:700px;top:970px;text-align:center">Our services go beyond transportation — we help create beautiful moments. Whether it's your wedding, a styled photo shoot, or a film project, we have the perfect car for every occasion.</p>

<div class="service-col" style="left:148px">
  <div class="badge"><svg viewBox="0 0 40 40" fill="none" stroke="#fff" stroke-width="1.8"><circle cx="16" cy="12" r="4"/><path d="M10 32l4-14h4l6 14z"/><circle cx="26" cy="13" r="3.5"/><path d="M24 18h4l2 14"/></svg></div>
  <h3>Weddings</h3><p>Elegant arrivals and grand departures.</p>
</div>
<div class="vrule" style="left:445px;top:1030px;height:160px"></div>
<div class="service-col" style="left:450px">
  <div class="badge"><svg viewBox="0 0 40 40" fill="none" stroke="#fff" stroke-width="1.8"><rect x="7" y="17" width="19" height="14" rx="2"/><path d="M26 21l7-4v14l-7-4"/><circle cx="12" cy="11" r="4"/><circle cx="22" cy="11" r="4"/></svg></div>
  <h3>Film &amp; Commercials</h3><p>Iconic vehicles for screen productions.</p>
</div>
<div class="vrule" style="left:755px;top:1030px;height:160px"></div>
<div class="service-col" style="left:754px">
  <div class="badge"><svg viewBox="0 0 40 40" fill="none" stroke="#fff" stroke-width="1.8"><rect x="7" y="13" width="26" height="18" rx="3"/><path d="M15 13l2-4h6l2 4"/><circle cx="20" cy="22" r="5"/></svg></div>
  <h3>Photo Shoots</h3><p>Picture-perfect cars for styled sessions.</p>
</div>

<!-- about -->
<div class="arch-frame" style="left:140px;top:1274px;width:390px;height:460px"></div>
<div class="photo arch" role="img" aria-label="Groom leaning on a silver vintage car with the bride nearby, tall cypress trees behind" style="left:148px;top:1266px;width:390px;height:460px;background:linear-gradient(180deg,#6f7c5a 0%,#3f4a33 40%,#8e9296 70%,#5a5a58 100%)"></div>
<div class="about-text" style="top:1320px">
  <div class="eyebrow">About Us</div>
  <h2 class="h2" style="margin-top:6px;font-size:39px">Crafted for Unforgettable Celebrations</h2>
  <p style="margin-top:20px">At WestyKolory.pl, we believe a wedding car should be more than just transportation — it should be part of the story. Founded by automotive and wedding enthusiasts, we've combined passion and precision to offer the finest cars, handpicked for style, performance, and beauty.</p>
  <p style="margin-top:16px">We are a team of automotive enthusiasts and wedding professionals who came together with one goal: to redefine what it means to travel in style on your big day. Our fleet features only the most elegant and iconic vehicles — each hand-selected for its timeless design, luxurious comfort, and powerful presence.</p>
</div>
<span class="btn btn-gold" style="left:591px;top:1639px;width:125px;height:42px">Read More</span>

<!-- every detail -->
<div class="floral" role="img" aria-label="Watercolour floral decoration" style="left:-60px;top:1900px;width:340px;height:260px"></div>
<h2 class="abs center h2" style="top:1796px">Every Detail, Perfected</h2>
<p class="abs lead" style="left:330px;width:540px;top:1846px;text-align:center">We combine sophistication, comfort, and flawless service — so your grand entrance feels effortless.</p>

<div class="feature-col" style="left:74px">
  <div class="badge"><svg viewBox="0 0 40 40" fill="none" stroke="#fff" stroke-width="1.8"><rect x="10" y="8" width="20" height="25" rx="2"/><path d="M14 15l2 2 3-3M14 23l2 2 3-3M22 16h5M22 24h5"/></svg></div>
  <h3>Impeccable Standards</h3><p>We maintain our vehicles to the<br>highest level of luxury...</p>
</div>
<div class="vrule" style="left:339px;top:1910px;height:185px"></div>
<div class="feature-col" style="left:344px">
  <div class="badge"><svg viewBox="0 0 40 40" fill="none" stroke="#fff" stroke-width="1.8"><circle cx="20" cy="15" r="5"/><path d="M11 33c0-6 4-10 9-10s9 4 9 10z"/><path d="M15 10h10"/></svg></div>
  <h3>Elegant Chauffeurs</h3><p>Our professional drivers are dis-<br>creet, punctual...</p>
</div>
<div class="vrule" style="left:599px;top:1910px;height:185px"></div>
<div class="feature-col" style="left:604px">
  <div class="badge"><svg viewBox="0 0 40 40" fill="none" stroke="#fff" stroke-width="1.8"><circle cx="16" cy="12" r="4"/><path d="M10 32l4-14h4l6 14z"/><path d="M26 10c3 0 5 2 5 5s-2 5-5 5"/></svg></div>
  <h3>Wedding-Ready Styling</h3><p>Decor options and custom details<br>to match your wedding theme.</p>
</div>
<div class="vrule" style="left:859px;top:1910px;height:185px"></div>
<div class="feature-col" style="left:870px">
  <div class="badge"><svg viewBox="0 0 40 40" fill="none" stroke="#fff" stroke-width="1.8"><rect x="8" y="10" width="24" height="22" rx="2"/><path d="M8 16h24M14 7v6M26 7v6"/><path d="M15 24a5 5 0 1 0 5-5"/></svg></div>
  <h3>Flexible Booking</h3><p>We work around your timeline —<br>with hourly, half-day...</p>
</div>

<!-- collection -->
<div class="abs collection-band"></div>
<h2 class="abs center h2" style="top:2268px">Explore Our Prestigious Collection</h2>
<p class="abs lead" style="left:280px;width:640px;top:2321px;text-align:center">From iconic classics to modern luxury, our fleet is handpicked to make your entrance unforgettable. Every car is maintained to the highest standards and comes with a uniformed chauffeur.</p>
<span class="btn btn-gold" style="left:514px;top:2380px;width:172px;height:40px">View All Vehicles</span>
<div class="photo collection-photo" role="img" aria-label="Bride in a white gown stepping from a white vintage convertible in front of a classical palace"></div>

<!-- why -->
<div class="floral" role="img" aria-label="Watercolour floral decoration" style="left:930px;top:3020px;width:300px;height:280px"></div>
<div class="abs eyebrow" style="left:122px;top:3140px">Why Choose Us</div>
<h2 class="abs h2" style="left:122px;top:3166px;width:480px">Where Elegance Meets Excellence</h2>

<div class="why-item" style="top:3262px">
  <div class="badge badge-sm"><svg viewBox="0 0 40 40" fill="none" stroke="#fff" stroke-width="2"><path d="M7 26v-5l4-7h18l4 7v5z"/><circle cx="13" cy="27" r="3"/><circle cx="27" cy="27" r="3"/></svg></div>
  <div><h3>Exclusive Fleet</h3><p>Luxury and exotic cars tailored for weddings.</p></div>
</div>
<div class="why-item" style="top:3350px">
  <div class="badge badge-sm"><svg viewBox="0 0 40 40" fill="none" stroke="#fff" stroke-width="2"><circle cx="20" cy="14" r="5"/><path d="M10 33c0-6 4-10 10-10s10 4 10 10z"/></svg></div>
  <div><h3>Professional Chauffeurs</h3><p>Polished, punctual, and experienced.</p></div>
</div>
<div class="why-item" style="top:3436px">
  <div class="badge badge-sm"><svg viewBox="0 0 40 40" fill="none" stroke="#fff" stroke-width="2"><path d="M20 8l3.5 7 7.5 1-5.5 5 1.5 7.5-7-3.7-7 3.7 1.5-7.5L9 16l7.5-1z"/></svg></div>
  <div><h3>Premium Experience</h3><p>Personalized service from booking to drop-off.</p></div>
</div>
<div class="why-item" style="top:3522px">
  <div class="badge badge-sm"><svg viewBox="0 0 40 40" fill="none" stroke="#fff" stroke-width="2"><path d="M8 21l6-6 6 4 6-4 6 6-12 11z"/></svg></div>
  <div><h3>Trusted Partner</h3><p>Proudly part of many unforgettable weddings.</p></div>
</div>

<div class="arch-frame" style="left:690px;top:3100px;width:390px;height:508px"></div>
<div class="photo arch" role="img" aria-label="Bride seated on the door of a silver vintage car with the groom standing beside her in a park" style="left:682px;top:3092px;width:390px;height:508px;background:linear-gradient(180deg,#7a6a3e 0%,#5b5632 35%,#9aa0a2 65%,#6a5b4a 100%)"></div>

<!-- faq -->
<h2 class="abs center h2" style="top:3684px">FAQ</h2>
<div class="faq-item" style="top:3746px;height:82px">
  <h3>Q: Are your cars rented with a chauffeur?</h3>
  <p>A: Yes, all vehicles include a professionally dressed chauffeur to ensure a smooth and luxurious experience.</p>
  <svg viewBox="0 0 12 12"><path d="M2 4l4 4 4-4" stroke="#d5b95d" stroke-width="1.5" fill="none"/></svg>
</div>
<div class="faq-item" style="top:3837px;height:49px">
  <h3>Q: Can I rent a car for just a few hours?</h3>
  <svg viewBox="0 0 12 12"><path d="M2 8l4-4 4 4" stroke="#d5b95d" stroke-width="1.5" fill="none"/></svg>
</div>
<div class="faq-item" style="top:3896px;height:49px">
  <h3>Q: Are your cars available for photo or video shoots?</h3>
  <svg viewBox="0 0 12 12"><path d="M2 8l4-4 4 4" stroke="#d5b95d" stroke-width="1.5" fill="none"/></svg>
</div>
<div class="faq-item" style="top:3955px;height:49px">
  <h3>Q: How far in advance should I book?</h3>
  <svg viewBox="0 0 12 12"><path d="M2 8l4-4 4 4" stroke="#d5b95d" stroke-width="1.5" fill="none"/></svg>
</div>

<!-- contact -->
<div class="floral" role="img" aria-label="Watercolour floral decoration" style="left:-40px;top:4190px;width:260px;height:250px"></div>
<form class="contact-card">
  <div class="field" style="left:24px;top:28px;width:208px"><label>Name*</label><div class="box"></div></div>
  <div class="field" style="left:240px;top:28px;width:208px"><label>Email*</label><div class="box"></div></div>
  <div class="field" style="left:24px;top:90px;width:208px"><label>Address*</label><div class="box"></div></div>
  <div class="field" style="left:240px;top:90px;width:208px"><label>Phone*</label><div class="box"></div></div>
  <div class="field" style="left:24px;top:153px;width:424px"><label>Send Your Message*</label><div class="box" style="height:100px"></div></div>
  <span class="btn btn-gold" style="left:171px;top:298px;width:130px;height:41px">Submit Now</span>
</form>
<svg class="abs" style="left:678px;top:4128px" width="74" height="44" viewBox="0 0 74 44" fill="none" stroke="#d5b95d" stroke-width="1.6"><path d="M10 36L4 12l18 12L37 4l15 20 18-12-6 24z"/><path d="M12 41h50"/></svg>
<h2 class="abs h2" style="left:678px;top:4166px;width:420px;font-size:40px">Let's Make Your Day Extraordinary</h2>
<p class="abs lead" style="left:680px;top:4268px;width:380px;font-size:11px">Have questions or ready to reserve your dream wedding car? We're here to help.</p>
<span class="btn btn-gold" style="left:680px;top:4318px;width:130px;height:40px">Contact Us</span>

<!-- footer -->
<footer class="site-footer">
  <div class="foot-brand"><span class="brand-dot"></span>WestaKolory.pl</div>
  <div class="foot-col" style="left:368px">
    <h4>Quick Links</h4>
    <ul><li>Home</li><li>About Us</li><li>Our Fleet</li><li>Services</li><li>Why Choose Us</li><li>FAQ</li><li>Contact</li></ul>
  </div>
  <div class="foot-col" style="left:586px">
    <h4>Contact Us</h4>
    <div class="contact-line" style="margin-top:22px"><svg viewBox="0 0 12 12"><path d="M2 1h3l1 3-2 1a7 7 0 0 0 3 3l1-2 3 1v3c-6 0-9-3-9-9z" fill="#d5b95d"/></svg>+48 501 220 874</div>
    <div class="contact-line" style="margin-top:20px"><svg viewBox="0 0 12 12"><rect x="1" y="2" width="10" height="8" fill="#d5b95d"/><path d="M1 2l5 4 5-4" stroke="#1c1c1c" fill="none"/></svg>kontakt@westykolory.pl</div>
    <div class="contact-line" style="margin-top:20px"><svg viewBox="0 0 12 12"><path d="M6 11S2 7 2 4.5a4 4 0 0 1 8 0C10 7 6 11 6 11z" fill="#d5b95d"/><circle cx="6" cy="4.5" r="1.4" fill="#1c1c1c"/></svg><span>WestyKolory.pl ul. Lipowa 8<br>00-950 Warszawa, Poland</span></div>
  </div>
  <div class="foot-col" style="left:866px">
    <h4>Subscribe Newsletter</h4>
    <p style="font-size:10.5px;color:#e8e8e8;margin-top:14px;padding-left:10px;line-height:1.4">Subscribe newsletter for the latest<br>offers and news</p>
    <div style="display:flex;margin-top:14px;width:260px;height:38px">
      <div style="flex:1;background:#fff;color:#8a8a8a;font-size:10px;display:flex;align-items:center;padding-left:26px">Enter Email...</div>
      <div style="width:48px;background:var(--gold);display:flex;align-items:center;justify-content:center"><svg width="14" height="10" viewBox="0 0 14 10"><path d="M1 5h11M8 1l4 4-4 4" stroke="#fff" stroke-width="1.5" fill="none"/></svg></div>
    </div>
  </div>
  <div class="to-top"><svg width="14" height="14" viewBox="0 0 14 14"><path d="M7 12V2M3 6l4-4 4 4" stroke="#1c1c1c" stroke-width="1.6" fill="none"/></svg></div>
  <div class="foot-rule"></div>
  <div class="copyright">© 2025 WestyKolory.pl – All rights reserved.</div>
</footer>

</body>
</html>
```